Meridale Bed Company Needs Business Card

Looking for a very nice looking business card. Creative but not extravagant. We sell beds and pillows across the U.S. and need something professional but catchy. I have attached the logo.

Name : Devin Holt
Title : President
Phone : (800) 471-2960
Email: sleep@quilmora.com
Website: www.quilmora.com

Can be single-sided or double-sided
horizontal or vertical

Can use Blues/Greys

Target Market(s)

Mass Market

Industry/Entity Type

Retail

Contact Information for Business Card

Name : Devin Holt
Title : President
Phone : (800) 471-2960
Email: sleep@quilmora.com
Website: www.quilmora.com

Requirements
Must have
• Clean, Modern, Smooth
• Can use Blues/Greys
• On the other side without the information - have something simple like www.quilmora.com or our logo
Nice to have
• Surprise me
Should not have
• Nothing crazy, nothing cluttered

```html
<!DOCTYPE html>
<html lang="en">
<head>
<meta charset="utf-8">
<title>Quilmora Business Card</title>
<link rel="stylesheet" href="https://fonts.googleapis.com/css2?family=Arimo:wght@400;700&display=swap">
<style>
  :root {
    --backdrop: #2a2b2e;
    --brand-blue: #34a8dc;
    --brand-blue-deep: #1f8fc6;
    --brand-blue-light: #4bb6e6;
    --paper: #ffffff;
    --paper-shade: #ececec;
    --rule-grey: #8c8c8c;
    --ink-light: #ffffff;
  }
  * { margin: 0; padding: 0; box-sizing: border-box; }
  html, body {
    width: 1200px;
    height: 843px;
    overflow: hidden;
    background: var(--backdrop);
    font-family: "Arimo", Arial, sans-serif;
  }
  .stage {
    width: 1200px;
    height: 843px;
    display: flex;
    flex-direction: column;
    align-items: center;
    justify-content: center;
    gap: 50px;
  }
  .card {
    position: relative;
    width: 600px;
    height: 343px;
    overflow: hidden;
    box-shadow: 0 10px 28px rgba(0, 0, 0, 0.45);
  }

  /* Back side */
  .card--back {
    background: linear-gradient(160deg, var(--brand-blue-light) 0%, var(--brand-blue) 55%, var(--brand-blue-deep) 100%);
    display: flex;
    flex-direction: column;
    align-items: center;
    justify-content: center;
  }
  .card--back .wordmark {
    color: var(--ink-light);
    font-size: 92px;
    font-weight: 400;
    letter-spacing: 2px;
    line-height: 1;
  }
  .card--back .back-url {
    margin-top: 40px;
    color: var(--ink-light);
    opacity: 0.85;
    font-size: 15px;
    letter-spacing: 6px;
  }

  /* Front side */
  .card--front {
    background: linear-gradient(180deg, var(--paper) 0%, var(--paper) 45%, var(--paper-shade) 62%);
  }
  .card--front .wave {
    position: absolute;
    inset: 0;
    width: 100%;
    height: 100%;
  }
  .card--front .wordmark {
    position: absolute;
    top: 62px;
    left: 0;
    right: 0;
    text-align: center;
    color: var(--brand-blue);
    font-size: 84px;
    font-weight: 400;
    letter-spacing: 2px;
    line-height: 1;
  }
  .contact {
    position: absolute;
    left: 92px;
    top: 218px;
    color: var(--ink-light);
    text-align: center;
    width: 330px;
  }
  .contact .name {
    font-size: 18px;
    font-weight: 700;
  }
  .contact .title {
    font-weight: 400;
    font-size: 16px;
  }
  .contact .lines {
    margin-top: 6px;
    font-size: 14px;
  }
  .contact .label { font-weight: 700; }
  .contact .web {
    margin-top: 8px;
    font-size: 14px;
    letter-spacing: 4px;
  }
</style>
</head>
<body>
  <main class="stage">
    <section class="card card--back" aria-label="Card back">
      <div class="wordmark">quilmora</div>
      <div class="back-url">www.quilmora.com</div>
    </section>

    <section class="card card--front" aria-label="Card front">
      <svg class="wave" viewBox="0 0 600 343" preserveAspectRatio="none" aria-hidden="true">
        <defs>
          <linearGradient id="bandFill" x1="0" y1="0" x2="0" y2="1">
            <stop offset="0" stop-color="#3aaee0"/>
            <stop offset="1" stop-color="#2596cc"/>
          </linearGradient>
        </defs>
        <path d="M0,200 Q300,206 600,262 L600,343 L0,343 Z" fill="url(#bandFill)"/>
        <path d="M0,192 Q300,198 600,254" fill="none" stroke="var(--rule-grey)" stroke-width="3"/>
      </svg>
      <div class="wordmark">quilmora</div>
      <div class="contact">
        <div class="name">Devin Holt <span class="title">- President</span></div>
        <div class="lines"><span class="label">P:</span> (800) 471-2960 &nbsp;<span class="label">E:</span> sleep@quilmora.com</div>
        <div class="web">www.quilmora.com</div>
      </div>
    </section>
  </main>
</body>
</html>
```